Waste, Recycling & Food Waste Signage

We need 3 simple signs made to identify our waste, recycling and food waste bins. The signs should read
1. Food Scraps Only
2. Recycling Only
3. Trash
We'd like a simple logo to identify each. This simple logo or graphic will help our residents identify which bin to place their waste. We will be putting these signs in our parks and public spaces. The signs will either be affixed above the bin or on the bin. They need to be easily identifiable from a distance.
I've seen some use the following colors
1. Food Scraps Only (green sign)
2. Recycling Only (blue sign)
3. Trash (black sign)
Target Market(s)
Residents, general public
Requirements
Must have
- Need it to be simple and easy to see.

```html
<!DOCTYPE html>
<html lang="en">
<head>
<meta charset="UTF-8">
<title>Waste Bin Signage</title>
<link href="https://fonts.googleapis.com/css2?family=Open+Sans:wght@700;800&display=swap" rel="stylesheet">
<style>
  :root {
    --canvas: #ffffff;
    --frame-border: #8a8a8a;
    --recycling-blue: #3d7be8;
    --food-green: #3e7e57;
    --trash-black: #000000;
    --sign-text: #ffffff;
  }
  html, body {
    margin: 0;
    padding: 0;
    width: 1200px;
    height: 1200px;
    overflow: hidden;
    background: var(--canvas);
  }
  .signage-set {
    width: 1200px;
    height: 1200px;
    display: flex;
    align-items: center;
    justify-content: center;
    gap: 40px;
  }
  .sign {
    width: 340px;
    height: 340px;
    box-sizing: border-box;
    background: #fff;
    border: 3px solid var(--frame-border);
    border-radius: 12px;
    padding: 10px;
  }
  .sign-face {
    width: 100%;
    height: 100%;
    display: flex;
    flex-direction: column;
    align-items: center;
    justify-content: space-between;
    padding: 8px 0 10px;
    box-sizing: border-box;
    color: var(--sign-text);
    font-family: "Open Sans", Arial, sans-serif;
    font-weight: 800;
    text-align: center;
  }
  .sign--recycling .sign-face { background: var(--recycling-blue); }
  .sign--food .sign-face { background: var(--food-green); }
  .sign--trash .sign-face { background: var(--trash-black); }
  .sign-title, .sign-only {
    margin: 0;
    font-size: 33px;
    line-height: 1.1;
    letter-spacing: 0.2px;
  }
  .sign-emblem {
    width: 210px;
    height: 210px;
    display: block;
  }
</style>
</head>
<body>
  <main class="signage-set">
    <section class="sign sign--recycling">
      <div class="sign-face">
        <h2 class="sign-title">RECYCLING</h2>
        <svg class="sign-emblem" viewBox="0 0 100 100" aria-label="Recycling arrows">
          <circle cx="50" cy="50" r="47" fill="none" stroke="#fff" stroke-width="2.6"/>
          <g id="recycle-arrow" fill="#fff">
            <polygon points="42,25 52,19 60,22 72,43 64,48 56,34 48,40"/>
            <polygon points="60,51 78,39 78,58"/>
          </g>
          <use href="#recycle-arrow" transform="rotate(120 50 50)"/>
          <use href="#recycle-arrow" transform="rotate(240 50 50)"/>
        </svg>
        <p class="sign-only">ONLY</p>
      </div>
    </section>

    <section class="sign sign--food">
      <div class="sign-face">
        <h2 class="sign-title">FOOD SCRAPS</h2>
        <svg class="sign-emblem" viewBox="0 0 100 100">
          <circle cx="50" cy="50" r="47" fill="none" stroke="#fff" stroke-width="2.6"/>
          <circle cx="50" cy="50" r="38" fill="#4f8e67" role="img" aria-label="Illustration of a banana peel in white outline"/>
        </svg>
        <p class="sign-only">ONLY</p>
      </div>
    </section>

    <section class="sign sign--trash">
      <div class="sign-face">
        <h2 class="sign-title">TRASH</h2>
        <svg class="sign-emblem" viewBox="0 0 100 100" aria-label="Trash can">
          <circle cx="50" cy="50" r="47" fill="none" stroke="#fff" stroke-width="2.6"/>
          <rect x="45" y="19" width="10" height="4" rx="1" fill="none" stroke="#fff" stroke-width="1.6"/>
          <rect x="26" y="23" width="48" height="7" rx="1.5" fill="#fff"/>
          <polygon points="29,32 71,32 67,80 33,80" fill="#fff"/>
          <g stroke="#000" stroke-width="2.2" stroke-linecap="round">
            <line x1="36" y1="36" x2="38" y2="76"/>
            <line x1="43" y1="36" x2="44" y2="76"/>
            <line x1="50" y1="36" x2="50" y2="76"/>
            <line x1="57" y1="36" x2="56" y2="76"/>
            <line x1="64" y1="36" x2="62" y2="76"/>
          </g>
        </svg>
        <p class="sign-only">ONLY</p>
      </div>
    </section>
  </main>
</body>
</html>
```